Marlowe Group needs a business card

I would like the card to be simple but modern and elegant.
I like black and white.
or black and gold.
we are a private finance lender and also are involved in property and property developments.

please look at the business card photos i provided i would like M.G only one one side and all the other details on the other side use fonts that tie in with my theme.

Industry/Entity Type

Finance

Contact Information for Business Card

Marlowe Group (M.G) Daniel Marlowe M: 0413586207 E: danmarl@inboxmail.test

Font styles to use
Other font styles liked:
• Use fonts that would reflect our business

Colors
000000
ffffff

Requirements
Must have
• one side of details
• other side has either M.G or Marlowe Group like in the photos provided

```html
<!DOCTYPE html>
<html lang="en">
<head>
<meta charset="utf-8">
<title>Marlowe Group – Business Card</title>
<link rel="stylesheet" href="https://fonts.googleapis.com/css2?family=Cinzel:wght@400;700&family=Lato:wght@400;700&display=swap">
<style>
  :root {
    --backdrop: #808080;
    --card-light: #ffffff;
    --card-dark: #000000;
    --ink: #111111;
    --ink-soft: #222222;
    --rule: #c8c8c8;
    --shadow: rgba(0, 0, 0, 0.45);
  }
  * { margin: 0; padding: 0; box-sizing: border-box; }
  html, body {
    width: 1200px;
    height: 900px;
    overflow: hidden;
    background: var(--backdrop);
  }
  .canvas {
    position: relative;
    width: 1200px;
    height: 900px;
  }
  .card {
    position: absolute;
    top: 309px;
    width: 281px;
    height: 282px;
    border-radius: 22px;
    box-shadow: 2px 4px 6px var(--shadow);
  }
  .card--front {
    left: 306px;
    background: var(--card-light);
    color: var(--ink);
    text-align: center;
  }
  .card--back {
    left: 613px;
    background: var(--card-dark);
    display: flex;
    align-items: center;
    justify-content: center;
  }
  .brand-square {
    position: absolute;
    left: 112px;
    top: 44px;
    width: 56px;
    height: 56px;
    border: 2px solid var(--ink);
  }
  .brand-name {
    position: absolute;
    left: 0;
    right: 0;
    top: 110px;
    font-family: "Cinzel", serif;
    font-weight: 400;
    font-size: 22px;
    letter-spacing: 0.3px;
    color: var(--ink);
  }
  .contact {
    position: absolute;
    left: 0;
    right: 0;
    top: 177px;
  }
  .contact__name {
    font-family: "Cinzel", serif;
    font-weight: 700;
    font-size: 13px;
    letter-spacing: 0.4px;
    color: var(--ink);
  }
  .contact__rule {
    width: 140px;
    height: 1px;
    margin: 5px auto 4px;
    background: var(--rule);
  }
  .contact__line {
    font-family: "Lato", sans-serif;
    font-size: 13px;
    line-height: 16px;
    color: var(--ink-soft);
  }
  .contact__label { font-weight: 700; }
  .back-mark {
    font-family: "Cinzel", serif;
    font-weight: 400;
    font-size: 52px;
    letter-spacing: 2px;
    color: var(--card-light);
  }
</style>
</head>
<body>
  <main class="canvas">
    <section class="card card--front" aria-label="Business card front">
      <div class="brand-square" aria-hidden="true"></div>
      <h1 class="brand-name">Marlowe Group</h1>
      <div class="contact">
        <p class="contact__name">DANIEL MARLOWE</p>
        <div class="contact__rule"></div>
        <p class="contact__line"><span class="contact__label">M:</span> 0413586207</p>
        <p class="contact__line"><span class="contact__label">E:</span> danmarl@inboxmail.test</p>
      </div>
    </section>
    <section class="card card--back" aria-label="Business card back">
      <p class="back-mark">M.G</p>
    </section>
  </main>
</body>
</html>
```